Need Flyer for Our Real estate Agency

Need to run General Campaign for our agency with Start of New Year as our theme ..Must have an agent's picture on the DL..
Address:
27 / 486Brindle rd, Marsden VIC 3047
Ph:03 9412 7306
email:info@kovalinrealestate.com.au
www.kovalinrealestate.com.au
Something like as attached picture..
Target Market(s)
Home Buyers
Industry/Entity Type
Real Estate Agent
Requirements
Must have
- Our Logo Colours

```html
<!DOCTYPE html>
<html lang="en">
<head>
<meta charset="utf-8">
<title>Kovalin Real Estate – New Year Campaign</title>
<link rel="stylesheet" href="https://fonts.googleapis.com/css2?family=Lato:wght@300;400;700;900&display=swap">
<style>
  :root {
    --page: #e9e7e4;
    --navy-deep: #081d4a;
    --navy: #0d2c6b;
    --blue-bright: #1559b0;
    --maroon: #7b1421;
    --white: #ffffff;
    --silver: #c9ccd2;
    --photo-warm: #b98a72;
    --photo-cool: #2c3f5e;
  }
  * { box-sizing: border-box; margin: 0; padding: 0; }
  html, body {
    width: 1200px; height: 1192px; overflow: hidden;
    background: var(--page);
    font-family: "Lato", Arial, sans-serif;
    color: var(--white);
  }
  .flyer {
    position: absolute; left: 120px; width: 960px; height: 456px;
    overflow: hidden;
    box-shadow: 0 6px 16px rgba(0,0,0,.25);
  }
  .flyer--appraisal { top: 112px; background: linear-gradient(120deg, var(--navy) 0%, var(--navy-deep) 100%); }
  .flyer--team { top: 640px; background: linear-gradient(100deg, var(--blue-bright) 0%, var(--navy) 45%, var(--navy-deep) 100%); }

  .hero-shape { position: absolute; left: 0; top: 0; }

  .brand {
    position: absolute; width: 360px; text-align: center;
  }
  .brand__name {
    display: block; font-weight: 400; font-size: 50px; letter-spacing: 6px; line-height: 1;
  }
  .brand__tag {
    display: block; margin-top: 8px; font-size: 11px; letter-spacing: 4px;
    border-top: 1px solid var(--white); padding-top: 6px; width: 240px; margin-left: auto; margin-right: auto;
  }

  .headline {
    position: absolute; left: 480px; width: 440px; top: 212px;
    text-align: center; font-weight: 300; font-size: 32px; line-height: 47px;
  }
  .subline {
    position: absolute; left: 460px; width: 480px; top: 322px;
    text-align: center; font-size: 15px; font-weight: 400;
  }
  .subline strong { font-weight: 700; }

  .band {
    position: absolute; left: 0; right: 0; bottom: 0;
    background: var(--maroon);
    border-top: 3px solid var(--white);
  }
  .flyer--appraisal .band { height: 66px; }
  .flyer--team .band { height: 66px; }

  .call-pill {
    position: absolute; height: 46px; border-radius: 23px;
    background: var(--white); color: var(--maroon);
    display: flex; align-items: center; justify-content: center; gap: 10px;
    font-weight: 700; font-size: 20px; white-space: nowrap;
    box-shadow: 0 3px 6px rgba(0,0,0,.25);
  }
  .call-pill svg { width: 22px; height: 22px; }
  .flyer--appraisal .call-pill { left: 516px; width: 366px; top: 370px; }
  .flyer--team .call-pill { left: 52px; width: 364px; top: 403px; }

  .appraisal-note {
    position: absolute; left: 520px; width: 360px; top: 424px;
    text-align: center; font-size: 17px;
  }

  .team-title {
    position: absolute; left: 48px; top: 44px;
    font-weight: 300; font-size: 56px; letter-spacing: 1px; line-height: 1;
  }
  .team-photo {
    position: absolute; left: 2px; top: 140px; width: 548px; height: 250px;
    background: linear-gradient(180deg, rgba(44,63,94,0) 0%, var(--photo-cool) 55%, #1e2f4e 100%),
                radial-gradient(ellipse at 50% 30%, var(--photo-warm) 0%, transparent 60%);
  }
  .contacts { position: absolute; left: 584px; top: 242px; list-style: none; }
  .contacts li {
    display: flex; align-items: center; gap: 12px; height: 41px; font-size: 17px;
  }
  .contacts svg { width: 18px; height: 18px; }
  .address {
    position: absolute; left: 490px; top: 415px; font-size: 17px; white-space: nowrap;
  }
</style>
</head>
<body>

<section class="flyer flyer--appraisal">
  <svg class="hero-shape" width="480" height="456" viewBox="0 0 480 456">
    <defs>
      <linearGradient id="heroTones" x1="0" y1="0" x2="1" y2="1">
        <stop offset="0" stop-color="#d9c3b4"/>
        <stop offset=".45" stop-color="#b96a63"/>
        <stop offset="1" stop-color="#2d3e5d"/>
      </linearGradient>
    </defs>
    <path d="M402 0 Q472 200 386 456 L470 456 Q520 220 460 0 Z" fill="var(--silver)"/>
    <path d="M402 0 Q462 200 386 456 L404 456 Q484 220 418 0 Z" fill="var(--white)"/>
    <path d="M0 0 H402 Q458 200 380 456 H0 Z" fill="url(#heroTones)" role="img" aria-label="Photo: two hands sheltering a small red model house"/>
  </svg>

  <div class="brand" style="left:520px; top:118px;">
    <span class="brand__name">KOVALIN</span>
    <span class="brand__tag">REAL ESTATE</span>
  </div>

  <p class="headline">Curios to know what your<br>home is worth?</p>
  <p class="subline">START OF NEW YEAR WITH <strong>KOVALIN</strong> AND FIND OUT!</p>

  <div class="band"></div>
  <a class="call-pill">CALL US NOW!
    <svg viewBox="0 0 24 24"><circle cx="12" cy="12" r="10" fill="none" stroke="currentColor" stroke-width="2"/><path d="M8.5 7.5c.6-.6 1.4-.5 1.8.2l.8 1.5c.3.6.1 1.2-.4 1.6l-.6.4c.5 1.2 1.4 2.1 2.6 2.6l.4-.6c.4-.5 1-.7 1.6-.4l1.5.8c.7.4.8 1.2.2 1.8l-.8.8c-3.4.6-8.1-4.1-7.5-7.5z" fill="currentColor"/></svg>
    03 9412 7306</a>
  <p class="appraisal-note">For Free property Appraisal</p>
</section>

<section class="flyer flyer--team">
  <h1 class="team-title">MEET THE TEAM</h1>
  <div class="team-photo" role="img" aria-label="Photo: four agents of the team in suits"></div>

  <div class="brand" style="left:522px; top:130px;">
    <span class="brand__name">KOVALIN</span>
    <span class="brand__tag">REAL ESTATE</span>
  </div>

  <ul class="contacts">
    <li><svg viewBox="0 0 24 24"><circle cx="12" cy="12" r="10" fill="none" stroke="#fff" stroke-width="2"/><path d="M8.5 7.5c.6-.6 1.4-.5 1.8.2l.8 1.5c.3.6.1 1.2-.4 1.6l-.6.4c.5 1.2 1.4 2.1 2.6 2.6l.4-.6c.4-.5 1-.7 1.6-.4l1.5.8c.7.4.8 1.2.2 1.8l-.8.8c-3.4.6-8.1-4.1-7.5-7.5z" fill="#fff"/></svg>03 9412 7306</li>
    <li><svg viewBox="0 0 24 24"><circle cx="12" cy="12" r="10" fill="none" stroke="#fff" stroke-width="2"/><rect x="6.5" y="8" width="11" height="8" fill="#fff"/><path d="M6.5 8l5.5 4.5L17.5 8" fill="none" stroke="var(--navy)" stroke-width="1.3"/></svg>info@kovalinrealestate.com.au</li>
    <li><svg viewBox="0 0 24 24" fill="none" stroke="#fff" stroke-width="1.6"><circle cx="12" cy="12" r="10"/><ellipse cx="12" cy="12" rx="4" ry="10"/><path d="M2 12h20M4 7h16M4 17h16"/></svg>www.kovalinrealestate.com.au</li>
  </ul>

  <div class="band"></div>
  <a class="call-pill">CALL US NOW!
    <svg viewBox="0 0 24 24"><circle cx="12" cy="12" r="10" fill="none" stroke="currentColor" stroke-width="2"/><path d="M8.5 7.5c.6-.6 1.4-.5 1.8.2l.8 1.5c.3.6.1 1.2-.4 1.6l-.6.4c.5 1.2 1.4 2.1 2.6 2.6l.4-.6c.4-.5 1-.7 1.6-.4l1.5.8c.7.4.8 1.2.2 1.8l-.8.8c-3.4.6-8.1-4.1-7.5-7.5z" fill="currentColor"/></svg>
    03 9412 7306</a>
  <p class="address">27 / 486Brindle rd, Marsden VIC 3047</p>
</section>

</body>
</html>
```